Veranix - Solution provider in business consulting

Veranix is a swiss based company providing solutions for developing markets. The business covers various fields of business consulting, such as supply chain, product costs, quality management and manufacturing management. The Business operates in a efficient, straight and solution oriented manner.
The final design should communicate these characteristics. Asian people as well as as western people shall identify the qualities of the company at first sight.
The customer needs business cards with a simple view but an recognizable design, printed in high quality. Engraved elements such as the globe or simple words are possible.
Available colors are: (RAL)
102/102/102
51/102/102
153/204/153
255/102/51
Font: Calibri

```html
<!DOCTYPE html>
<html lang="en">
<head>
<meta charset="utf-8">
<title>Veranix – Business Card</title>
<link rel="stylesheet" href="https://fonts.googleapis.com/css2?family=Carlito:wght@400;700&display=swap">
<style>
  :root {
    --backdrop: #e6e2dc;
    --card-front: #f7f7f5;
    --card-back: #8f8f8f;
    --ink-grey: #666666;
    --foil-silver: #f4f4f4;
    --foil-shade: #d9d9d9;
    --shadow: rgba(0, 0, 0, 0.18);
  }
  * { margin: 0; padding: 0; box-sizing: border-box; }
  html, body {
    width: 1200px;
    height: 795px;
    overflow: hidden;
    background: var(--backdrop);
    font-family: "Carlito", "Calibri", sans-serif;
  }
  .stage {
    position: relative;
    width: 1200px;
    height: 795px;
  }
  .card {
    position: absolute;
    top: 229px;
    width: 520px;
    height: 336px;
    border-radius: 3px;
    box-shadow: 0 6px 18px var(--shadow);
  }
  .card--front {
    left: 50px;
    background: var(--card-front);
  }
  .card--back {
    left: 630px;
    background: var(--card-back);
    color: var(--foil-silver);
  }

  /* Front: wordmark */
  .wordmark {
    position: absolute;
    left: 0;
    right: 0;
    top: 50%;
    transform: translateY(-50%);
    display: flex;
    align-items: center;
    justify-content: center;
    gap: 14px;
  }
  .wordmark__dot {
    width: 38px;
    height: 38px;
    border-radius: 50%;
    background: var(--foil-shade);
  }
  .wordmark__name {
    font-size: 54px;
    font-weight: 400;
    letter-spacing: 2px;
    color: var(--ink-grey);
    text-transform: lowercase;
  }

  /* Back: accent and contact block */
  .back-accent {
    position: absolute;
    top: 34px;
    right: 40px;
    width: 72px;
    height: 72px;
    border-radius: 50%;
    background: var(--foil-silver);
  }
  .contact {
    position: absolute;
    left: 40px;
    top: 118px;
    right: 40px;
  }
  .contact__name {
    font-size: 24px;
    font-weight: 400;
    line-height: 1.1;
  }
  .contact__role {
    font-size: 14px;
    margin-bottom: 22px;
  }
  .contact__address,
  .contact__lines {
    font-size: 15px;
    line-height: 1.32;
    list-style: none;
  }
  .contact__address { margin-bottom: 2px; }
  .contact__lines li {
    display: flex;
    align-items: center;
    gap: 8px;
  }
  .contact__icon {
    width: 12px;
    height: 12px;
    flex: none;
  }
</style>
</head>
<body>
<main class="stage">

  <section class="card card--front" aria-label="Business card front">
    <div class="wordmark">
      <span class="wordmark__dot"></span>
      <span class="wordmark__name">veranix</span>
    </div>
  </section>

  <section class="card card--back" aria-label="Business card back">
    <div class="back-accent"></div>
    <div class="contact">
      <p class="contact__name">Marco Feldt</p>
      <p class="contact__role">CEO</p>
      <p class="contact__address">Veranix GmbH<br>Lindenweg 14, 9240 Uzwil<br>Switzerland</p>
      <ul class="contact__lines">
        <li>
          <svg class="contact__icon" viewBox="0 0 12 12" aria-hidden="true">
            <path d="M2 1h2.5l1 3-1.5 1a7 7 0 0 0 3 3l1-1.5 3 1V11c-5 0-9-4-9-10z" fill="var(--foil-silver)"/>
          </svg>
          +41 71 555 0142
        </li>
        <li>
          <svg class="contact__icon" viewBox="0 0 12 12" aria-hidden="true">
            <rect x="3" y="0.5" width="6" height="11" rx="1" fill="none" stroke="var(--foil-silver)" stroke-width="1.2"/>
            <circle cx="6" cy="9.5" r="0.8" fill="var(--foil-silver)"/>
          </svg>
          +41 79 555 0187
        </li>
        <li>
          <svg class="contact__icon" viewBox="0 0 12 12" aria-hidden="true">
            <rect x="0.6" y="2" width="10.8" height="8" fill="none" stroke="var(--foil-silver)" stroke-width="1.2"/>
            <path d="M0.6 2.4 6 6.5l5.4-4.1" fill="none" stroke="var(--foil-silver)" stroke-width="1.2"/>
          </svg>
          marco.feldt@veranix.ch
        </li>
        <li>
          <svg class="contact__icon" viewBox="0 0 12 12" aria-hidden="true">
            <circle cx="6" cy="6" r="5.3" fill="none" stroke="var(--foil-silver)" stroke-width="1.2"/>
            <path d="M0.7 6h10.6M6 0.7c-3 3.2-3 7.4 0 10.6M6 0.7c3 3.2 3 7.4 0 10.6" fill="none" stroke="var(--foil-silver)" stroke-width="1"/>
          </svg>
          www.veranix.ch
        </li>
      </ul>
    </div>
  </section>

</main>
</body>
</html>
```